Stylish Business Cards Wanted

- DOUBLE SIDED Design Required -

High end, edgy cards for a corporate and personal stylist. Must include logo,
Name: Belinda Harwick
Title: Director and Stylist
telephone : +61 8 7142 5809
email: belinda@theloombriefing.example
website: theloombriefing.example
Tag: Corporate Workwear & Uniform Specialist | Personal Stylist
Would like nice icons for telephone, email, website

Target Market(s)

Businesses wanting stylish uniforms, people wanting stylish wardrobes

Industry/Entity Type

Corporate Workwear Stylist

Contact Information for Business Card

I would like black, white and gold foiling incorporated in the design - possibly a touch of the other colours on my branding guide attached Name: Belinda Harwick Title: Director and Stylist telephone : +61 8 7142 5809 email: belinda@theloombriefing.example website: theloombriefing.example Tag: Corporate Workwear & Uniform Specialist | Personal Stylist Would like nice icons for telephone, email, website

Font styles to use
Other font styles liked:
• Raleway

Colors

Designer to choose colors to be used in the design.

Requirements
Must have
• Gold foil accents

```html
<!DOCTYPE html>
<html lang="en">
<head>
<meta charset="utf-8">
<title>The Loom Briefing – Business Card</title>
<link rel="stylesheet" href="https://fonts.googleapis.com/css2?family=Raleway:wght@300;400;600&family=Arimo:wght@400&display=swap">
<style>
  :root {
    --ink: #151515;
    --paper: #ffffff;
    --gold: #d8b453;
    --rule: #9a9a9a;
    --back: #17181a;
    --backdrop: #2a2a2b;
    --card-w: 440px;
    --card-h: 720px;
  }
  * { box-sizing: border-box; margin: 0; padding: 0; }
  html, body { width: 1200px; height: 1108px; overflow: hidden; }
  body {
    background: var(--backdrop);
    display: flex;
    align-items: center;
    justify-content: center;
    gap: 60px;
    font-family: "Arimo", Arial, sans-serif;
  }
  .card {
    position: relative;
    width: var(--card-w);
    height: var(--card-h);
    border-radius: 26px;
    overflow: hidden;
    box-shadow: 0 18px 40px rgba(0,0,0,.45);
  }
  /* Front */
  .card--front {
    background: var(--paper);
    color: var(--ink);
    display: flex;
    flex-direction: column;
    align-items: center;
  }
  .brand {
    margin-top: 150px;
    display: flex;
    align-items: center;
    gap: 12px;
    font-family: "Raleway", sans-serif;
    font-weight: 600;
    font-size: 34px;
    letter-spacing: .02em;
    color: var(--ink);
  }
  .brand__mark {
    width: 14px; height: 14px;
    background: var(--gold);
  }
  .person {
    margin-top: 190px;
    text-align: center;
  }
  .person__name {
    font-family: "Raleway", sans-serif;
    font-weight: 600;
    font-size: 32px;
    letter-spacing: .01em;
    text-transform: uppercase;
  }
  .person__title {
    margin-top: 2px;
    font-family: "Raleway", sans-serif;
    font-weight: 300;
    font-size: 19px;
    color: var(--gold);
    text-transform: uppercase;
  }
  .icon-row {
    margin-top: 26px;
    display: flex;
    align-items: center;
    gap: 6px;
    width: 300px;
  }
  .icon-row__rule { flex: 1; height: 1px; background: var(--rule); }
  .icon {
    width: 30px; height: 30px;
    border-radius: 5px;
    background: var(--ink);
    display: flex; align-items: center; justify-content: center;
  }
  .contact {
    margin-top: 10px;
    text-align: center;
    font-size: 18px;
    line-height: 1.35;
  }
  .tagline {
    position: absolute;
    left: 0; right: 0; bottom: 0;
    height: 140px;
    background: var(--ink);
    color: var(--paper);
    display: flex; flex-direction: column;
    align-items: center; justify-content: center;
    font-size: 19px;
    line-height: 1.4;
    text-align: center;
  }
  /* Back */
  .card--back {
    background: var(--back);
    display: flex;
    align-items: center;
    justify-content: center;
  }
  .back__pattern {
    position: absolute; inset: 0;
    background: linear-gradient(160deg, #1d1e20 0%, #141517 100%);
  }
  .back__brand {
    position: relative;
    margin-top: 300px;
    display: flex; align-items: center; gap: 10px;
    font-family: "Raleway", sans-serif;
    font-weight: 600;
    font-size: 26px;
    color: var(--paper);
  }
  .back__brand .brand__mark { width: 11px; height: 11px; }
</style>
</head>
<body>
  <section class="card card--front" aria-label="Card front">
    <div class="brand"><span class="brand__mark"></span>The Loom Briefing</div>

    <div class="person">
      <h1 class="person__name">Belinda Harwick</h1>
      <p class="person__title">Director and Stylist</p>
    </div>

    <div class="icon-row">
      <span class="icon-row__rule"></span>
      <span class="icon" aria-label="Telephone">
        <svg width="20" height="20" viewBox="0 0 20 20" fill="none" stroke="#fff" stroke-width="1.6" stroke-linecap="round" stroke-linejoin="round">
          <path d="M3 6c0-2 2-3 7-3s7 1 7 3v1h-3V5.5H6V7H3z"/>
          <rect x="5" y="9" width="10" height="7" rx="1"/>
          <circle cx="10" cy="12.5" r="1.4"/>
        </svg>
      </span>
      <span class="icon" aria-label="Email">
        <svg width="20" height="20" viewBox="0 0 20 20" fill="none" stroke="#fff" stroke-width="1.6" stroke-linejoin="round">
          <rect x="3" y="5" width="14" height="10"/>
          <path d="M3 5l7 6 7-6M3 15l5-5M17 15l-5-5"/>
        </svg>
      </span>
      <span class="icon" aria-label="Website">
        <svg width="20" height="20" viewBox="0 0 20 20" fill="none" stroke="#fff" stroke-width="1.5">
          <circle cx="10" cy="10" r="6.5"/>
          <ellipse cx="10" cy="10" rx="3" ry="6.5"/>
          <path d="M3.5 10h13"/>
        </svg>
      </span>
      <span class="icon-row__rule"></span>
    </div>

    <address class="contact" style="font-style:normal">
      <div>+61 8 7142 5809</div>
      <div>belinda@theloombriefing.example</div>
      <div>theloombriefing.example</div>
    </address>

    <footer class="tagline">
      <span>Corporate Workwear &amp; Uniform Specialist</span>
      <span>Personal Stylist</span>
    </footer>
  </section>

  <section class="card card--back" aria-label="Card back">
    <div class="back__pattern" role="img" aria-label="Faint tonal repeating brand pattern on black"></div>
    <div class="back__brand"><span class="brand__mark"></span>The Loom Briefing</div>
  </section>
</body>
</html>
```